Business Card for a Jewellery Brand

Business card for an upscale jewellery brand. Attached is the brand logo and icon and color board. I am looking for two card versions: one for the founder and one is generic. The card should be elegant and convey upscale and premium feel. I am open to both square and rectangle card shapes.

Industry/Entity Type

Jewelry

Contact Information for Business Card

Two cards: (1) Sunela Parvaniya (Founder) (2) General
(1) Sunela Parvaniya card should have Name: Sunela Parvaniya, Title: Founder Email id: sunela@quiremo.com.au. Phone no: +61452913307
(2) Generic card should have Email id: info@quiremo.com.au. Phone no: +61436207518

Requirements
Must have
• Workmark
• ICON
• Phone no
• Email ID
• ABN: 58219740312 (Note: ABN is Business number in Australia)
• Website: www.quiremo.com.au
• Instagram: quiremo_jewellery
• Facebook: @quiremojewellery
Nice to have
• Tagline

```html
<!DOCTYPE html>
<html lang="en">
<head>
<meta charset="utf-8">
<title>Quiremo Business Cards</title>
<link rel="stylesheet" href="https://fonts.googleapis.com/css2?family=Source+Sans+3:wght@400;600&display=swap">
<style>
  :root {
    --stage: #000000;
    --card: #e59894;
    --ink: #ffffff;
  }
  * { margin: 0; padding: 0; box-sizing: border-box; }
  html, body {
    width: 1200px;
    height: 900px;
    overflow: hidden;
    background: var(--stage);
    font-family: "Source Sans 3", "Myriad Pro", sans-serif;
    color: var(--ink);
  }
  .stage { position: relative; width: 1200px; height: 900px; }
  .card {
    position: absolute;
    top: 275px;
    width: 477px;
    height: 293px;
    background: var(--card);
  }
  .card--front {
    left: 116px;
    border-radius: 0 58px 0 68px;
  }
  .card--back {
    left: 622px;
    top: 276px;
    height: 292px;
    border-radius: 58px 0 68px 0;
  }
  .holder { position: absolute; left: 20px; top: 54px; }
  .holder__name { font-size: 18px; font-weight: 600; line-height: 1; }
  .holder__role { font-size: 13px; font-weight: 400; margin-top: 3px; line-height: 1; }
  .abn { position: absolute; left: 20px; top: 116px; font-size: 13px; line-height: 1; }
  .abn__label { font-weight: 600; }
  .contacts {
    position: absolute;
    right: 27px;
    top: 34px;
    list-style: none;
    text-align: right;
  }
  .contacts__item {
    display: flex;
    justify-content: flex-end;
    align-items: center;
    gap: 7px;
    font-size: 13px;
    line-height: 19.5px;
    letter-spacing: 0.1px;
  }
  .contacts__icon { width: 10px; height: 10px; flex: none; }
  .brand-mark {
    position: absolute;
    left: 50%;
    border: 2.5px solid var(--ink);
    border-radius: 50%;
  }
  .card--front .brand-mark { top: 130px; width: 72px; height: 72px; margin-left: -36px; }
  .card--back .brand-mark { top: 68px; width: 96px; height: 96px; margin-left: -48px; border-width: 3px; }
  .brand {
    position: absolute;
    left: 0;
    right: 0;
    text-align: center;
    font-weight: 400;
    text-transform: uppercase;
    line-height: 1;
    white-space: nowrap;
  }
  .card--front .brand { top: 214px; font-size: 42px; letter-spacing: 8px; padding-left: 8px; }
  .card--back .brand { top: 172px; font-size: 56px; letter-spacing: 10px; padding-left: 10px; }
</style>
</head>
<body>
<main class="stage">
  <section class="card card--front" aria-label="Founder card">
    <div class="holder">
      <p class="holder__name">Sunela Parvaniya</p>
      <p class="holder__role">Founder</p>
    </div>
    <p class="abn"><span class="abn__label">ABN:</span> 58219740312</p>
    <ul class="contacts">
      <li class="contacts__item">+61452913307
        <svg class="contacts__icon" viewBox="0 0 10 10" aria-hidden="true"><path d="M2 0.8 L3.6 2.9 L2.8 4 Q4 6.2 6 7.2 L7.1 6.4 L9.2 8 L8.2 9.4 Q3.5 8.8 0.6 1.8 Z" fill="#fff"/></svg>
      </li>
      <li class="contacts__item">sunela@quiremo.com.au
        <svg class="contacts__icon" viewBox="0 0 10 10" aria-hidden="true"><rect x="0.5" y="2" width="9" height="6.5" fill="#fff"/><path d="M0.8 2.4 L5 5.6 L9.2 2.4" fill="none" stroke="#e59894" stroke-width="0.9"/></svg>
      </li>
      <li class="contacts__item">www.quiremo.com.au
        <svg class="contacts__icon" viewBox="0 0 10 10" aria-hidden="true"><circle cx="5" cy="5" r="4.6" fill="#fff"/><path d="M0.6 5 H9.4 M5 0.5 Q2.4 5 5 9.5 M5 0.5 Q7.6 5 5 9.5" fill="none" stroke="#e59894" stroke-width="0.7"/></svg>
      </li>
      <li class="contacts__item">quiremo_jewellery
        <svg class="contacts__icon" viewBox="0 0 10 10" aria-hidden="true"><rect x="0.5" y="0.5" width="9" height="9" rx="2" fill="#fff"/></svg>
      </li>
      <li class="contacts__item">@quiremojewellery
        <svg class="contacts__icon" viewBox="0 0 10 10" aria-hidden="true"><circle cx="5" cy="5" r="5" fill="#fff"/></svg>
      </li>
    </ul>
    <span class="brand-mark" aria-hidden="true"></span>
    <p class="brand">Quiremo</p>
  </section>

  <section class="card card--back" aria-label="Brand card">
    <span class="brand-mark" aria-hidden="true"></span>
    <p class="brand">Quiremo</p>
  </section>
</main>
</body>
</html>
```